Business Card Design Project - del varosi group

dear Sirs

we need business card design for our group ( DEL Varosi Group ) , i have got the Logo design of our group from pixel harbor in previous , so all need details relating to our group i think available with you, as well as the the chosen logo design

we hope to provide us with business card logo that to be appropaite and satisfactory to us .

thanks

note : logo design of our group is attached .
Updates

Reason: please extend the deadline of my project for additional 15 days because i didn't received appropriate design for our gruop yet . kindly beaware that i have received 77 design till now , supossed to send me 200-250 design at least . thanks

Target Market(s)

contents

name : Kerem EL Nadiri

position : Operation Manager

Industry/Entity Type

Business

Requirements
Must have

• person name

group logo
Nice to have
• logo color matching with back background

```html
<!DOCTYPE html>
<html lang="en">
<head>
<meta charset="utf-8">
<title>DEL Varosi Group – Business Card</title>
<link rel="stylesheet" href="https://fonts.googleapis.com/css2?family=Open+Sans:wght@400;600;700&display=swap">
<style>
  :root {
    --brand-blue: #1d5a9e;
    --brand-blue-dark: #164a86;
    --brand-blue-light: #3d7fc4;
    --card-white: #ffffff;
    --text-grey: #5f6368;
    --divider: #d4d6da;
    --stage: #e9eaec;
  }
  * { box-sizing: border-box; margin: 0; padding: 0; }
  html, body { width: 1200px; height: 758px; overflow: hidden; }
  body {
    background: var(--stage);
    font-family: "Open Sans", Arial, sans-serif;
    position: relative;
  }
  .card {
    position: absolute;
    top: 219px;
    width: 540px;
    height: 320px;
    border-radius: 26px;
    overflow: hidden;
    box-shadow: 0 6px 18px rgba(0,0,0,0.18);
  }
  .card-front { left: 40px; background: var(--card-white); }
  .card-back { left: 620px; background: var(--brand-blue); }

  .front-wave { position: absolute; inset: 0; width: 540px; height: 320px; }

  .brand-name {
    position: absolute;
    display: flex;
    align-items: center;
    gap: 12px;
    font-weight: 700;
    letter-spacing: 1px;
    line-height: 1.05;
  }
  .brand-name .mark {
    width: 14px; height: 14px;
    flex: none;
  }
  .card-front .brand-name {
    left: 40px; top: 108px;
    color: var(--brand-blue);
    font-size: 30px;
  }
  .card-front .brand-name .mark { background: var(--brand-blue); }
  .brand-name small { display: block; font-size: 17px; letter-spacing: 3px; }

  .divider {
    position: absolute;
    left: 272px; top: 40px;
    width: 1px; height: 135px;
    background: var(--divider);
  }
  .contact-block { position: absolute; left: 290px; top: 36px; }
  .person-name { color: var(--brand-blue); font-weight: 700; font-size: 21px; }
  .person-role { color: var(--text-grey); font-size: 13px; margin-bottom: 8px; }
  .contact-list { list-style: none; color: var(--text-grey); font-size: 13px; line-height: 19px; }
  .contact-list li { display: flex; align-items: center; gap: 6px; }
  .contact-list svg { width: 10px; height: 10px; fill: var(--text-grey); flex: none; }

  .address {
    position: absolute; left: 40px; top: 258px;
    color: var(--card-white); font-size: 13px; line-height: 18px;
  }

  .card-back .brand-name {
    left: 50%; top: 110px; transform: translateX(-50%);
    color: var(--card-white);
    font-size: 40px;
    white-space: nowrap;
  }
  .card-back .brand-name .mark { background: var(--card-white); width: 18px; height: 18px; }
  .card-back .brand-name small { font-size: 22px; letter-spacing: 4px; }
  .back-website {
    position: absolute; left: 0; right: 0; top: 240px;
    text-align: center; color: var(--card-white);
    font-size: 19px; letter-spacing: 1.5px;
  }
</style>
</head>
<body>

<section class="card card-front" aria-label="Business card front">
  <svg class="front-wave" viewBox="0 0 540 320" aria-hidden="true">
    <path d="M0,238 C150,190 320,222 540,198 L540,212 C320,236 150,206 0,254 Z" fill="var(--brand-blue-light)"/>
    <path d="M0,262 C150,214 320,242 540,222 L540,320 L0,320 Z" fill="var(--brand-blue)"/>
  </svg>

  <div class="brand-name">
    <span class="mark"></span>
    <span>DEL VAROSI<small>GROUP</small></span>
  </div>

  <div class="divider"></div>

  <div class="contact-block">
    <p class="person-name">Kerem EL Nadiri</p>
    <p class="person-role">Operation Manager</p>
    <ul class="contact-list">
      <li><svg viewBox="0 0 10 10"><rect x="2.5" y="0.5" width="5" height="9" rx="1"/></svg>+2348125550147</li>
      <li><svg viewBox="0 0 10 10"><path d="M2 0.5 L4 2.5 L3 4 C4 6 5 7 6.5 7.5 L7.5 6 L9.5 8 L8 9.5 C4 9 1 6 0.5 2 Z"/></svg>+2348125550147</li>
      <li><svg viewBox="0 0 10 10"><circle cx="5" cy="3" r="2.4"/><path d="M0.5 10 C1 6 9 6 9.5 10 Z"/></svg>+2348125550147</li>
      <li><svg viewBox="0 0 10 10"><rect x="0.5" y="2" width="9" height="6.5" rx="0.6"/></svg>name@varosigroup.com</li>
      <li><svg viewBox="0 0 10 10"><circle cx="5" cy="5" r="4.5"/></svg>www.website.com</li>
    </ul>
  </div>

  <p class="address">Street name, City<br>State, zip code</p>
</section>

<section class="card card-back" aria-label="Business card back">
  <div class="brand-name">
    <span class="mark"></span>
    <span>DEL VAROSI<small>GROUP</small></span>
  </div>
  <p class="back-website">www.website.com</p>
</section>

</body>
</html>
```